Carpentry framing business card and logo design

We need a logo that works well with baseball caps, tee shirts and sweat shirts. We are a carpentry framing company specializing in apartment complexes and large residential communities. We work in what is known as the tri state area southeastern Pennsylvania , New Jersey and northern Delaware . We would like to see die signs using the old English letter M and royal blue colors. Also we stress OSHA compliance and safety.

Industry/Entity Type

Residential

Contact Information for Business Card

Valdrick Construction Co Inc
4870 Quillford Lane
Ambler PA 19087
Dale Valdrick
dale1valdrick@norvexmail.com
267-815-0926

```html
<!DOCTYPE html>
<html lang="en">
<head>
<meta charset="utf-8">
<title>Valdrick Construction – Business Card</title>
<link rel="stylesheet" href="https://fonts.googleapis.com/css2?family=Cinzel:wght@600&family=Arimo:wght@400&display=swap">
<style>
  :root {
    --page-bg: #e9e4dc;
    --card-white: #fbfbfb;
    --card-black: #111111;
    --accent: #e3685a;
    --accent-deep: #d7574a;
    --ink: #141414;
    --text-light: #f4f4f4;
  }
  * { box-sizing: border-box; margin: 0; padding: 0; }
  html, body { width: 1200px; height: 818px; overflow: hidden; }
  body {
    background: var(--page-bg);
    display: flex;
    align-items: center;
    justify-content: center;
    font-family: "Arimo", Arial, sans-serif;
  }
  .card {
    width: 410px;
    height: 716px;
    background: var(--card-white);
    position: relative;
    overflow: hidden;
    box-shadow: 0 14px 36px rgba(0,0,0,0.22);
  }
  .brand {
    position: absolute;
    top: 150px;
    left: 0;
    right: 0;
    text-align: center;
    font-family: "Cinzel", Georgia, serif;
    font-weight: 600;
    color: var(--ink);
    font-size: 30px;
    line-height: 1.25;
    letter-spacing: 2px;
  }
  .contact-panel {
    position: absolute;
    left: 0; right: 0;
    top: 380px;
    bottom: 92px;
    background: var(--card-black);
    border-top: 8px solid var(--accent);
    padding: 34px 30px 0 34px;
  }
  .person-name {
    font-family: "Cinzel", Georgia, serif;
    font-weight: 600;
    color: var(--accent);
    font-size: 31px;
    letter-spacing: 1px;
    margin-bottom: 26px;
  }
  .contact-list { list-style: none; }
  .contact-list li {
    display: flex;
    align-items: center;
    gap: 12px;
    color: var(--text-light);
    font-size: 17px;
    margin-bottom: 14px;
  }
  .contact-list svg { width: 16px; height: 16px; flex: none; fill: var(--accent); }
  .safety-band {
    position: absolute;
    left: 0; right: 0; bottom: 0;
    height: 92px;
    background: var(--accent-deep);
    display: flex;
    align-items: center;
    justify-content: center;
    color: var(--ink);
    font-size: 21px;
    letter-spacing: 0.3px;
  }
</style>
</head>
<body>
  <article class="card">
    <div class="brand">Valdrick<br>Construction</div>

    <section class="contact-panel">
      <h1 class="person-name">Dale Valdrick</h1>
      <ul class="contact-list">
        <li>
          <svg viewBox="0 0 24 24" aria-hidden="true"><path d="M6.6 10.8a15.1 15.1 0 0 0 6.6 6.6l2.2-2.2c.3-.3.7-.4 1-.2 1.1.4 2.3.6 3.6.6.6 0 1 .4 1 1V20c0 .6-.4 1-1 1A17 17 0 0 1 3 4c0-.6.4-1 1-1h3.5c.6 0 1 .4 1 1 0 1.3.2 2.5.6 3.6.1.3 0 .7-.2 1z"/></svg>
          267-815-0926
        </li>
        <li>
          <svg viewBox="0 0 24 24" aria-hidden="true"><path d="M2 5h20v14H2z M4 7v.3l8 5.2 8-5.2V7z" fill-rule="evenodd"/></svg>
          dale1valdrick@norvexmail.com
        </li>
        <li>
          <svg viewBox="0 0 24 24" aria-hidden="true"><path d="M12 2a7 7 0 0 0-7 7c0 5.2 7 13 7 13s7-7.8 7-13a7 7 0 0 0-7-7zm0 9.5A2.5 2.5 0 1 1 12 6.5a2.5 2.5 0 0 1 0 5z"/></svg>
          4870 Quillford Lane Ambler PA 19087
        </li>
      </ul>
    </section>

    <footer class="safety-band">OSHA compliance and SAFETY 1st</footer>
  </article>
</body>
</html>
```